Redesign of the UI of a customer service platform

To improve the user experience of our customers, we need a new design for our agent interface of our customer service platform (nolvi.com).
The focus will be on the dashboard and the inbox screens (see attached) along with the common UI elements (Buttons, menu, fonts, forms...)
We want a simple and distinctive design

Target Market(s)

Worldwide

Industry/Entity Type

It Service

Number of Pages Required

3 page

Font styles to use
Sans Serif

Requirements
Must have
• New Onboarding page: this is a new page that is shown to user the first time they login to the platform. This will replace the current onboarding screen (setup SMS, Setup widget...etc)
• Dashboard page: to access important information and activate services (see screenshot from current site)
• Inbox page: to manage all the interactions with customers. (see screenshot from current site)
• UI elements (buttons, menus, forms, tables, fonts, color palette)

```html
<!DOCTYPE html>
<html lang="en">
<head>
<meta charset="utf-8">
<title>Nolvi — Inbox</title>
<link href="https://fonts.googleapis.com/css2?family=Open+Sans:wght@400;600&display=swap" rel="stylesheet">
<style>
:root{
  --bar:#3b3b3b;
  --bar-line:#4a4a4a;
  --bar-active:#2f2f2f;
  --brand:#f15a24;
  --page:#ececec;
  --panel:#ffffff;
  --head-tint:#f8f7e4;
  --text:#3f3f3f;
  --muted:#8a8a8a;
  --soft:#666666;
  --icon:#bbbbbb;
  --line:#e2e2e2;
  --bubble:#dcf0f2;
  --badge-red:#e8212b;
  --badge-amber:#f5a623;
  --online:#3fb93f;
  --avatar-a:#c9a98f;
  --avatar-b:#b89a86;
  --btn:#efefef;
}
*{box-sizing:border-box;margin:0;padding:0}
html,body{width:1200px;height:831px;overflow:hidden}
body{font-family:"Open Sans",Arial,sans-serif;background:var(--page);color:var(--text);position:relative}
.abs{position:absolute}
.avatar{border-radius:50%;background:radial-gradient(circle at 50% 40%,var(--avatar-a),var(--avatar-b) 70%,#7c8593 71%);border:2px solid #fff;box-shadow:0 0 0 1px #e5e5e5}

/* top bar */
.topbar{left:0;top:0;width:1200px;height:83px;background:var(--bar)}
.brand{left:0;top:0;width:83px;height:83px;background:var(--brand);color:#fff;font-size:11px;font-weight:600}
.brand-dot{position:absolute;left:29px;top:17px;width:26px;height:26px;border-radius:50%;border:3px solid #fff}
.brand-name{position:absolute;left:0;top:52px;width:83px;text-align:center;white-space:nowrap}
.nav{left:83px;top:0;display:flex;height:83px}
.nav-item{width:84px;height:83px;border-right:1px solid var(--bar-line);color:#fff;font-size:13.5px;position:relative}
.nav-item.active{background:var(--bar-active)}
.nav-item svg{position:absolute;left:28px;top:16px;width:28px;height:28px}
.nav-label{position:absolute;left:0;top:52px;width:84px;text-align:center;white-space:nowrap}
.badge{position:absolute;top:17px;left:50px;width:22px;height:22px;border-radius:50%;color:#fff;font-size:11px;font-weight:600;display:flex;align-items:center;justify-content:center}
.badge.red{background:var(--badge-red)}
.badge.amber{background:var(--badge-amber)}
.me{left:1131px;top:14px;width:56px;height:56px}
.online{left:1128px;top:15px;width:14px;height:14px;border-radius:50%;background:var(--online)}

/* conversation list */
.list{left:0;top:83px;width:343px;height:748px;background:var(--panel);border-right:1px solid var(--line)}
.list-head{height:83px;background:var(--head-tint);text-align:center;padding-top:20px;border-bottom:1px solid var(--line);position:relative}
.list-head h1{font-weight:400;font-size:18px}
.list-head p{font-size:12.5px;color:var(--muted);margin-top:2px}
.list-head svg{position:absolute;right:14px;top:38px}
.conv{height:84px;border-bottom:1px solid var(--line);position:relative}
.conv.selected{background:#f1f1f1}
.conv .avatar{position:absolute;left:13px;top:14px;width:56px;height:56px}
.conv-name{position:absolute;left:83px;top:22px;font-size:16px}
.conv-time{position:absolute;right:12px;top:12px;font-size:11px;color:var(--muted)}
.conv-preview{position:absolute;left:83px;top:47px;font-size:13px;color:var(--muted);display:flex;align-items:center;gap:6px;white-space:nowrap}
.agents{position:absolute;right:12px;top:30px;display:flex;gap:3px}
.agents .avatar{position:static;width:26px;height:26px;border-width:1px}

/* customer panel */
.profile{left:358px;top:97px;width:412px;height:720px;background:var(--panel)}
.actions{position:absolute;right:14px;top:15px;display:flex;gap:9px;align-items:center}
.btn{background:var(--btn);color:var(--muted);font-size:13px;height:23px;padding:0 10px;display:flex;align-items:center;gap:6px;border-radius:2px}
.kebab{width:4px;display:flex;flex-direction:column;gap:3px}
.kebab i{width:4px;height:4px;border-radius:50%;background:#aaa}
.big-avatar{position:absolute;left:151px;top:66px;width:110px;height:110px}
.p-name{position:absolute;top:186px;width:100%;text-align:center;font-size:16.5px}
.p-meta{position:absolute;top:219px;width:100%;display:flex;justify-content:center;gap:14px;font-size:13px;color:var(--muted)}
.p-meta span{display:flex;align-items:center;gap:6px}
.section{position:absolute;left:13px;right:13px;border-top:1px solid var(--line)}
.sec-title{display:flex;justify-content:space-between;align-items:center;padding-top:16px}
.sec-title h2{font-weight:400;font-size:16.5px}
.add{font-size:13px;color:var(--muted)}
.fields{margin-top:20px;font-size:12.5px}
.field{display:flex;height:24px;align-items:center;white-space:nowrap}
.field dt{width:104px;text-align:right;color:var(--muted);padding-right:12px}
.field dd{flex:1;color:var(--soft)}
.field dd.link{color:var(--brand)}
.field svg{margin-right:1px}
.show-all{text-align:center;color:var(--brand);font-size:12.5px;margin-top:12px;display:flex;justify-content:center;gap:6px;align-items:center}
.task{display:flex;height:24px;align-items:center;font-size:12.5px;color:var(--soft);white-space:nowrap}
.task .t{width:246px}
.task .d{width:80px}
.task .ic{flex:1;display:flex;justify-content:flex-end;align-items:center;gap:10px}
.empty{text-align:center;font-size:13px;color:var(--muted);margin-top:18px}

/* chat */
.chat{left:774px;top:97px;width:412px;height:720px;background:var(--panel)}
.chat .kebab{position:absolute;right:14px;top:18px}
.msg{position:absolute;display:flex;flex-direction:column;gap:5px}
.msg.in{left:86px;align-items:flex-start}
.msg.out{right:86px;align-items:flex-end}
.bubble{background:var(--bubble);font-size:13px;color:var(--soft);padding:3px 9px;line-height:1.6;border-radius:2px;position:relative}
.msg.in .bubble:first-child::before{content:"";position:absolute;left:-6px;top:7px;border:6px solid transparent;border-left:0;border-right-color:var(--bubble)}
.msg.out .bubble:first-child::after{content:"";position:absolute;right:-6px;top:7px;border:6px solid transparent;border-right:0;border-left-color:var(--bubble)}
.stamp{font-size:11px;color:var(--muted);margin-left:-10px}
.chat-avatar{position:absolute;width:56px;height:56px}
.composer-tools{position:absolute;right:14px;top:607px;display:flex;gap:9px;align-items:center}
.composer{position:absolute;left:13px;right:13px;top:632px;border-top:1px solid var(--line);padding-top:16px;font-size:13px;color:var(--muted)}
</style>
</head>
<body>

<header class="topbar abs">
  <div class="brand abs"><span class="brand-dot"></span><span class="brand-name">nolvi</span></div>
  <nav class="nav abs">
    <div class="nav-item active">
      <svg viewBox="0 0 28 28" fill="none" stroke="#fff" stroke-width="2"><path d="M3 16h7l1 3h6l1-3h7v8H3z" fill="#fff"/><path d="M14 3v9M10 8l4 4 4-4"/></svg>
      <span class="nav-label">Inbox</span><span class="badge red">4</span>
    </div>
    <div class="nav-item">
      <svg viewBox="0 0 28 28" fill="none" stroke="#fff" stroke-width="2"><rect x="5" y="4" width="16" height="20"/><path d="M9 10h8M9 14h8M9 18h4"/></svg>
      <span class="nav-label">Tasks</span><span class="badge amber">1</span>
    </div>
    <div class="nav-item">
      <svg viewBox="0 0 28 28" fill="#fff"><circle cx="14" cy="9" r="5"/><path d="M5 25c0-6 4-9 9-9s9 3 9 9z"/></svg>
      <span class="nav-label">Customers</span>
    </div>
    <div class="nav-item">
      <svg viewBox="0 0 28 28" fill="none" stroke="#fff" stroke-width="2"><path d="M3 5l22 9-22 9 4-9zM7 14h18"/></svg>
      <span class="nav-label">Campaigns</span>
    </div>
    <div class="nav-item">
      <svg viewBox="0 0 28 28"><text x="14" y="22" text-anchor="middle" fill="#fff" font-size="22" font-family="Open Sans,sans-serif">$</text></svg>
      <span class="nav-label">Payments</span>
    </div>
    <div class="nav-item">
      <svg viewBox="0 0 28 28" fill="#fff"><rect x="4" y="4" width="3" height="20"/><rect x="10" y="10" width="3" height="14"/><rect x="16" y="4" width="3" height="20"/><rect x="22" y="13" width="3" height="11"/></svg>
      <span class="nav-label">Reports</span>
    </div>
    <div class="nav-item">
      <svg viewBox="0 0 28 28" fill="#fff"><circle cx="14" cy="14" r="9"/><g stroke="#fff" stroke-width="4"><path d="M14 2v24M2 14h24M5.5 5.5l17 17M22.5 5.5l-17 17"/></g><circle cx="14" cy="14" r="3.5" fill="#3b3b3b"/></svg>
      <span class="nav-label">Settings</span>
    </div>
  </nav>
  <div class="avatar me abs" role="img" aria-label="Agent profile photo"></div>
  <span class="online abs"></span>
</header>

<aside class="list abs">
  <div class="list-head">
    <h1>Open Conversations</h1>
    <p>New or Assigned to me</p>
    <svg width="14" height="9" viewBox="0 0 14 9" fill="none" stroke="#f15a24" stroke-width="1.6"><path d="M1 1l6 6 6-6"/></svg>
  </div>

  <div class="conv">
    <div class="avatar" role="img" aria-label="Customer photo, Lena Marsh"></div>
    <span class="conv-name">Lena Marsh</span><span class="conv-time">2 mins ago</span>
    <span class="conv-preview"><svg width="13" height="11" viewBox="0 0 13 11" fill="#aaa"><path d="M0 5l13-5-3 11-4-4z"/></svg>Yes that would be great, please...</span>
    <div class="agents"><div class="avatar" role="img" aria-label="Assigned agent photo"></div></div>
  </div>
  <div class="conv selected">
    <div class="avatar" role="img" aria-label="Customer photo, Owen Hale"></div>
    <span class="conv-name">Owen Hale</span><span class="conv-time">9 mins ago</span>
    <span class="conv-preview"><svg width="14" height="11" viewBox="0 0 14 11" fill="#aaa"><rect x="0" y="0" width="14" height="8"/><rect x="4" y="9" width="6" height="2"/></svg>Hi, I need to know if there are...</span>
    <div class="agents"><div class="avatar" role="img" aria-label="Assigned agent photo"></div></div>
  </div>
  <div class="conv">
    <div class="avatar" role="img" aria-label="Customer photo, Tomas Reed"></div>
    <span class="conv-name">Tomas Reed</span><span class="conv-time">1 mins ago</span>
    <span class="conv-preview"><svg width="10" height="10" viewBox="0 0 10 10"><rect width="10" height="10" fill="#aaa"/></svg>The issue occured one more...</span>
    <div class="agents"><div class="avatar" role="img" aria-label="Assigned agent photo"></div></div>
  </div>
  <div class="conv">
    <div class="avatar" role="img" aria-label="Customer photo, Owen Hale"></div>
    <span class="conv-name">Owen Hale</span><span class="conv-time">2 mins ago</span>
    <span class="conv-preview"><svg width="14" height="11" viewBox="0 0 14 11" fill="none" stroke="#aaa" stroke-width="2"><path d="M6 1L1 5l5 4M1 5h7c4 0 5 3 5 6"/></svg>Yes that’s true we are not...</span>
    <div class="agents"><div class="avatar" role="img" aria-label="Assigned agent photo"></div><div class="avatar" role="img" aria-label="Assigned agent photo"></div></div>
  </div>
  <div class="conv">
    <div class="avatar" role="img" aria-label="Customer photo, Lena Marsh"></div>
    <span class="conv-name">Lena Marsh</span><span class="conv-time">3 mins ago</span>
    <span class="conv-preview"><svg width="13" height="11" viewBox="0 0 13 11" fill="#aaa"><path d="M0 5l13-5-3 11-4-4z"/></svg>Yes that would be great, please...</span>
    <div class="agents"><div class="avatar" role="img" aria-label="Assigned agent photo"></div></div>
  </div>
</aside>

<section class="profile abs">
  <div class="actions">
    <span class="btn"><svg width="12" height="10" viewBox="0 0 12 10" fill="none" stroke="#aaa" stroke-width="2"><path d="M1 5l3 3 7-7"/></svg>Close</span>
    <span class="btn"><svg width="12" height="10" viewBox="0 0 12 10" fill="none" stroke="#aaa" stroke-width="2"><path d="M0 5h10M6 1l4 4-4 4"/></svg>Transfer</span>
    <span class="kebab"><i></i><i></i><i></i></span>
  </div>
  <div class="avatar big-avatar" role="img" aria-label="Customer photo, Owen Hale"></div>
  <div class="p-name">Owen Hale</div>
  <div class="p-meta">
    <span><svg width="14" height="11" viewBox="0 0 14 11" fill="#aaa"><rect width="14" height="8"/><rect x="4" y="9" width="6" height="2"/></svg>Campaigns</span>
    <span><svg width="10" height="13" viewBox="0 0 10 13" fill="#aaa"><path d="M5 0a5 5 0 0 1 5 5c0 3-5 8-5 8S0 8 0 5a5 5 0 0 1 5-5z"/><circle cx="5" cy="5" r="2" fill="#fff"/></svg>United States</span>
  </div>

  <div class="section" style="top:264px">
    <div class="sec-title"><h2>Details</h2><span class="add">+ ADD</span></div>
    <dl class="fields">
      <div class="field"><dt>#ID :</dt><dd>41</dd><svg width="14" height="14" viewBox="0 0 14 14" fill="#bbb"><path d="M1 13l1-4 8-8 3 3-8 8z"/></svg></div>
      <div class="field"><dt>Email :</dt><dd class="link">owen.hale@mailbox.test</dd><svg width="14" height="14" viewBox="0 0 14 14" fill="#bbb"><path d="M1 13l1-4 8-8 3 3-8 8z"/></svg></div>
      <div class="field"><dt>Phone :</dt><dd class="link">+1(555)014 2290</dd><svg width="14" height="14" viewBox="0 0 14 14" fill="#bbb"><path d="M1 13l1-4 8-8 3 3-8 8z"/></svg></div>
      <div class="field"><dt>Address Line 1 :</dt><dd>418 Birchwood Lane</dd><svg width="14" height="14" viewBox="0 0 14 14" fill="#bbb"><path d="M1 13l1-4 8-8 3 3-8 8z"/></svg></div>
      <div class="field"><dt>City :</dt><dd>Millbrook</dd><svg width="14" height="14" viewBox="0 0 14 14" fill="#bbb"><path d="M1 13l1-4 8-8 3 3-8 8z"/></svg></div>
      <div class="field"><dt>State :</dt><dd>North Carolina</dd><svg width="14" height="14" viewBox="0 0 14 14" fill="#bbb"><path d="M1 13l1-4 8-8 3 3-8 8z"/></svg></div>
    </dl>
    <div class="show-all"><svg width="10" height="7" viewBox="0 0 10 7" fill="none" stroke="#f15a24" stroke-width="1.5"><path d="M1 1l4 4 4-4"/></svg>Show All</div>
  </div>

  <div class="section" style="top:512px">
    <div class="sec-title"><h2>Tasks</h2><span class="add">+ ADD</span></div>
    <div style="margin-top:14px">
      <div class="task"><span class="t">Verify customer identity</span><span class="d">2017-15-01</span><span class="ic"><svg width="14" height="11" viewBox="0 0 14 11" fill="none" stroke="#bbb" stroke-width="2"><path d="M1 5l4 4 8-8"/></svg><svg width="11" height="11" viewBox="0 0 11 11"></svg><svg width="11" height="13" viewBox="0 0 11 13" fill="#bbb"><rect x="0" y="1" width="11" height="2"/><rect x="1.5" y="4" width="8" height="9"/></svg></span></div>
      <div class="task"><span class="t">Check if the customer was billed twice</span><span class="d">2017-16-01</span><span class="ic"><svg width="14" height="11" viewBox="0 0 14 11" fill="none" stroke="#bbb" stroke-width="2"><path d="M1 5l4 4 8-8"/></svg><svg width="11" height="11" viewBox="0 0 11 11" stroke="#bbb" stroke-width="2"><path d="M1 1l9 9M10 1l-9 9"/></svg><svg width="11" height="13" viewBox="0 0 11 13" fill="#bbb"><rect x="0" y="1" width="11" height="2"/><rect x="1.5" y="4" width="8" height="9"/></svg></span></div>
    </div>
  </div>

  <div class="section" style="top:633px">
    <div class="sec-title"><h2>Notes</h2><span class="add">+ ADD</span></div>
    <p class="empty">Empty</p>
  </div>
</section>

<section class="chat abs">
  <span class="kebab"><i></i><i></i><i></i></span>

  <div class="avatar chat-avatar" role="img" aria-label="Customer photo" style="left:15px;top:37px"></div>
  <div class="msg in" style="top:44px">
    <span class="bubble">Hello</span>
    <span class="bubble">My CC got billed twice on subscription<br>renewal!</span>
  </div>

  <div class="avatar chat-avatar" role="img" aria-label="Agent photo" style="right:15px;top:166px"></div>
  <div class="msg out" style="top:172px">
    <span class="bubble">Hi Owen</span>
    <span class="bubble">Cay you please give me the last four<br>digits of your CC?</span>
    <span class="bubble">I need that for verification purposes</span>
  </div>

  <div class="avatar chat-avatar" role="img" aria-label="Customer photo" style="left:15px;top:323px"></div>
  <div class="msg in" style="top:328px"><span class="bubble">Ok, here you go 5411</span></div>

  <div class="avatar chat-avatar" role="img" aria-label="Agent photo" style="right:15px;top:402px"></div>
  <div class="msg out" style="top:407px"><span class="bubble">I will let billing know about this</span></div>

  <div class="avatar chat-avatar" role="img" aria-label="Customer photo" style="left:15px;top:481px"></div>
  <div class="msg in" style="top:486px">
    <span class="bubble">Yes that would be great, please do this<br>ASAP</span>
    <span class="stamp">2 mins ago</span>
  </div>

  <div class="composer-tools">
    <svg width="10" height="14" viewBox="0 0 10 14"><text x="5" y="12" text-anchor="middle" fill="#bbb" font-size="14" font-family="Open Sans,sans-serif">$</text></svg>
    <svg width="10" height="14" viewBox="0 0 10 14" fill="none" stroke="#bbb" stroke-width="1.5"><path d="M7 4v6a2 2 0 0 1-4 0V3a3 3 0 0 1 6 0"/></svg>
    <svg width="15" height="13" viewBox="0 0 15 13" fill="none" stroke="#bbb" stroke-width="1.5"><rect x="1" y="1" width="13" height="11"/><path d="M1 10l4-4 4 4 2-2 3 3"/></svg>
    <svg width="14" height="14" viewBox="0 0 14 14" fill="none" stroke="#bbb" stroke-width="1.5"><circle cx="7" cy="7" r="6"/><path d="M4 8.5c1.5 2 4.5 2 6 0"/><circle cx="5" cy="5.5" r=".6" fill="#bbb"/><circle cx="9" cy="5.5" r=".6" fill="#bbb"/></svg>
  </div>
  <div class="composer">Your Message...</div>
</section>

</body>
</html>
```